Dorian Vasko Consulting

I've the wording, and the rough layout. See attached MicroSoft Word File. I need a professional to make my postcard "look pretty".

Industry/Entity Type

Consulting

```html
<!DOCTYPE html>
<html lang="en">
<head>
<meta charset="utf-8">
<title>Dorian Vasko Consulting – Postcard</title>
<link href="https://fonts.googleapis.com/css2?family=Arimo:wght@400;700&display=swap" rel="stylesheet">
<style>
  :root {
    --brand-blue: #1d84b1;
    --ink-white: #ffffff;
    --frame-grey: #8a8a8a;
    --postage-ink: #444444;
    --line-grey: #555555;
    --page: #ffffff;
  }
  * { box-sizing: border-box; margin: 0; padding: 0; }
  html, body { width: 885px; height: 1200px; overflow: hidden; background: var(--page); }
  body { position: relative; font-family: "Arimo", Arial, sans-serif; color: var(--ink-white); }

  .card-front {
    position: absolute; left: 0; top: 0; width: 885px; height: 590px;
    background: var(--brand-blue); border: 1px solid #16648a;
  }
  .card-back {
    position: absolute; left: 0; top: 611px; width: 885px; height: 589px;
    background: var(--page); border: 1px solid var(--frame-grey);
  }
  .back-panel {
    position: absolute; left: 0; top: 0; width: 476px; height: 100%;
    background: var(--brand-blue); border: 2px solid #3a9cc6;
  }

  .headline {
    position: absolute; left: 38px;
    font-weight: 400; font-size: 37.5px; line-height: 44px; letter-spacing: 0.2px;
  }
  .headline strong { font-weight: 700; }
  .front-headline { top: 42px; }
  .back-headline { top: 31px; }

  .growth-chart { position: absolute; left: 0; top: 0; }

  .question-list {
    position: absolute; list-style: none;
    font-size: 12px; line-height: 14.6px; letter-spacing: -0.35px;
  }
  .front-questions { left: 38px; top: 264px; width: 474px; }
  .back-questions { left: 29px; top: 229px; width: 410px; }

  .pitch {
    position: absolute; font-size: 12px; line-height: 14.6px; letter-spacing: -0.35px;
  }
  .front-pitch { left: 531px; top: 144px; width: 333px; text-align: justify; }
  .front-pitch p { margin-bottom: 14.6px; }
  .back-pitch { left: 29px; top: 396px; width: 405px; }

  .site-url {
    position: absolute; left: 29px; top: 540px;
    font-weight: 700; font-size: 15.5px;
  }

  .postage {
    position: absolute; left: 770px; top: 48px;
    color: var(--postage-ink); font-weight: 700; font-size: 18px; line-height: 23px;
  }
  .address-line {
    position: absolute; left: 539px; width: 291px; height: 1px; background: var(--line-grey);
  }
</style>
</head>
<body>

<section class="card-front">
  <h1 class="headline front-headline">Learn Small Business<br>Success Secrets<br>only <strong>“insiders”</strong><br>know about:</h1>

  <svg class="growth-chart" width="885" height="250" viewBox="0 0 885 250" aria-hidden="false">
    <g fill="none" stroke="#ffffff" stroke-width="1.6">
      <polyline points="38,240 343,240 380,182 398,192 420,161 474,163 510,156 536,104 557,109 580,82"/>
      <polyline points="571,80 583,78 580,90"/>
    </g>
    <g fill="#ffffff">
      <circle cx="380" cy="182" r="3.5"/><circle cx="398" cy="192" r="3.5"/>
      <circle cx="420" cy="161" r="3.5"/><circle cx="474" cy="163" r="3.5"/>
      <circle cx="510" cy="156" r="3.5"/><circle cx="536" cy="104" r="3.5"/>
      <circle cx="557" cy="109" r="3.5"/>
    </g>
    <rect x="432" y="28" width="78" height="132" fill="#4a9dc2" opacity="0.55" role="img" aria-label="Outline of a businessman with briefcase climbing the growth line"/>
  </svg>

  <ol class="question-list front-questions">
    <li>1.For those people who almost bought from you but did not, what’s the real reason why they didn’t buy from you? (And what to do about it?)</li>
    <li>2.How to turn an ordinary service that the customer can find everywhere, into something that the customer has to buy from you and only you?</li>
    <li>3.How to turn customer’s “scope creeping”, from a business loss, into a prfit generator?</li>
    <li>4.What sort of person would be eager to sell to you at below fair market value?</li>
    <li>5.How to best utilize your limited operating capital?</li>
    <li>6.What sort of people would be a waste of time for your marketing effort?</li>
    <li>7.Other than money, how to motivate your employees?</li>
    <li>8.How to prevent your employees from stealing your business secrets? Setting up a competing business down the street from you? And worse still, taking your existing customers too?</li>
    <li>9.How to increase the perceived value of your products and services in the mind of your customers?</li>
    <li>10.How to market a commodity as a highly desired “must have” luxury item?</li>
    <li>11.How do you utilize a potentially bad situation and turn the situation into something positive? productive? and most importantly: Profitable???!!!</li>
  </ol>

  <div class="pitch front-pitch">
    <p>“Insiders” who know the answers to these tricky business problems, get ahead in business and life. And the deeper their understanding to these tricky business problems, the more successful they become. They have very little stress from their businesses; they work very few hours by building their businesses into "auto pilot". They have more free time to enjoy life.</p>
    <p>If you don't know how to solve these tricky business problems, you will find yourself struggling with your businesses. You will find yourself working very long hours, and you have a lot of stress from running your business. If you are not even aware of the existence of this aspect of running a business, your business will not survive. You will become part of the statistic: 80% of businesses fail.</p>
    <p>What specific problems are slowing you down, or keeping you stuck, from reaching your ultimate goals? What specific challenges are causing you all the Stresses? Headaches? Frustrations?</p>
    <p>If your situation continues, how will it negatively impact you from achieving your personal fulfillment? If these problems and challenges could be solved, what are the benefits to you? Short term benefits? Long term benefits?</p>
    <p>To learn how to overcome these problems and challenges:</p>
  </div>
</section>

<section class="card-back">
  <div class="back-panel">
    <h2 class="headline back-headline">Learn Small Business<br>Success Secrets<br>only <strong>“insiders”</strong><br>know about:</h2>

    <ol class="question-list back-questions">
      <li>1.How to make people want to have what you have for sale?</li>
      <li>2.How to turn new customers into repeat customers?</li>
      <li>3.How to make repeat customers comeback more often?</li>
      <li>4.How to spend less time with each customer, yet increase your profit on each business transaction?</li>
      <li>5.How to get more operating capital?</li>
      <li>6.How to buy low and sell high?</li>
      <li>7.How to manage employees and contractors?</li>
      <li>8.Which marketing methods are total waste of time and money?</li>
    </ol>

    <p class="pitch back-pitch">Why do 80% of all businesses fail??? Because their owners didn’t know what “business insiders” know. They worked very long hours, they had a lot of stresses and headaches, and in the end, due to their lack of business know-how, their businesses failed and they were left with a bunch of debt, a broken heart and sometimes a broken family too. Don’t become one of them! Become a real “insider”, run a successful business without stress and enjoy life! To find out more:</p>

    <p class="site-url">www.InsiderBusinessPlaybook.com</p>
  </div>

  <p class="postage">Postage<br>Paid</p>
  <span class="address-line" style="top:269px"></span>
  <span class="address-line" style="top:326px"></span>
  <span class="address-line" style="top:383px"></span>
  <span class="address-line" style="top:439px"></span>
</section>

</body>
</html>
```